Luxury Business Card Design for High-End Window Treatments

Gilded Slatworks
Custom Plantation Shutters & Architectural Shading Systems

⸻

BACK

Daniel Trevick
Owner

Custom Interior & Exterior Window Treatments

919-555-0148
gildedslatworks.com

I have included a picture that I’m hoping we can use on the back, but I’m also wondering if you can get rid of the ladder? Should we get rid of shutters , shades and blinds underneath Gilded Slatworks?

Target Market(s)

High-end residential homeowners, custom home builders, architects, interior designers, and luxury renovation clients seeking premium plantation shutters and motorized architectural shading systems.

Industry/Entity Type

Custom Window treatments

Contact Information for Business Card

Front Gilded Slatworks Custom Plantation Shutters Motorized Architectural Shading Systems BACK Daniel Trevick Owner 919-555-0148 GildedSlatworks.com Custom Interior & Exterior Window Treatments By Appointment

Requirements
Nice to have
• Not 100% sure on nice to halves or the color but you can definitely check out my website to get a better understanding of what I’m trying to do

```html
<!DOCTYPE html>
<html lang="en">
<head>
<meta charset="utf-8">
<title>Gilded Slatworks — Business Card</title>
<link rel="stylesheet" href="https://fonts.googleapis.com/css2?family=Cormorant+Garamond:ital,wght@0,500;1,500&family=Open+Sans:ital,wght@0,400;0,700;0,800;1,400&display=swap">
<style>
  :root {
    --page: #0c0c0c;
    --card-black: #161616;
    --gold: #c9a44a;
    --gold-light: #e8cd7e;
    --gold-deep: #a7782a;
    --ink-white: #f2f2f2;
    --photo-dark: #1d1d1d;
    --photo-mid: #3a3a3a;
  }
  * { box-sizing: border-box; margin: 0; padding: 0; }
  html, body { width: 1200px; height: 963px; overflow: hidden; background: var(--page); }
  .canvas { position: relative; width: 1200px; height: 963px; }

  .card {
    position: absolute; left: 232px; width: 735px; height: 420px;
    overflow: hidden; box-shadow: 0 10px 30px rgba(0,0,0,.6);
  }
  .card--front { top: 40px; }
  .card--back { top: 503px; background: var(--card-black); }

  .card__photo {
    position: absolute; inset: 0;
    background:
      linear-gradient(180deg, rgba(0,0,0,.35) 0%, rgba(0,0,0,.15) 55%, rgba(0,0,0,.45) 100%),
      linear-gradient(160deg, var(--photo-mid) 0%, var(--photo-dark) 45%, #2c2c2c 75%, var(--photo-mid) 100%);
  }

  .frame {
    position: absolute; left: 40px; right: 40px; top: 32px; bottom: 32px;
    border: 1.5px solid var(--gold); border-bottom: none;
  }
  .frame__bottom {
    position: absolute; left: -1.5px; right: -1.5px; bottom: 0;
    display: flex; align-items: center; transform: translateY(50%);
  }
  .frame__line { height: 1.5px; background: var(--gold); }
  .frame__line--lead { width: 50px; }
  .frame__line--rest { flex: 1; }
  .frame__caption {
    padding: 0 8px; font-family: "Open Sans", sans-serif; color: var(--ink-white); white-space: nowrap;
  }
  .card--front .frame__caption { font-weight: 700; font-size: 15px; letter-spacing: .2px; }
  .card--back .frame__caption { font-weight: 400; font-size: 19px; }

  .brand-name {
    font-family: "Cormorant Garamond", serif; font-weight: 500; color: var(--gold);
    line-height: .92;
  }
  .brand-lines {
    font-family: "Cormorant Garamond", serif; font-style: italic; font-weight: 500; color: var(--gold);
    display: flex; gap: 30px;
  }

  .front-brand { position: absolute; left: 150px; top: 92px; text-align: center; }
  .front-brand .brand-name { font-size: 96px; }
  .front-brand .brand-lines { font-size: 34px; justify-content: center; margin-top: 14px; }

  .back-brand { position: absolute; left: 80px; top: 110px; width: 300px; text-align: center; }
  .back-brand .brand-name { font-size: 58px; }
  .back-brand .brand-lines { font-size: 22px; justify-content: center; gap: 18px; margin-top: 12px; }

  .divider { position: absolute; left: 405px; top: 95px; width: 1.5px; height: 190px; background: var(--gold); }

  .contact { position: absolute; left: 432px; top: 120px; font-family: "Open Sans", sans-serif; }
  .contact__name { font-weight: 800; font-size: 27px; color: var(--gold-light); letter-spacing: .5px; text-transform: uppercase; }
  .contact__role { font-style: italic; font-size: 19px; color: var(--ink-white); margin-top: -2px; }
  .contact__list { list-style: none; margin-top: 26px; }
  .contact__item { display: flex; align-items: center; gap: 8px; font-size: 21px; color: var(--ink-white); margin-bottom: 4px; }
  .contact__icon { width: 16px; height: 16px; flex: none; }
</style>
</head>
<body>
<main class="canvas">

  <section class="card card--front" aria-label="Card front">
    <div class="card__photo" role="img" aria-label="Muted greyscale photograph of a covered porch with columns, shuttered windows and shrubs"></div>
    <div class="front-brand">
      <div class="brand-name">Gilded<br>Slatworks</div>
      <div class="brand-lines"><span>Shutters</span><span>Shades</span><span>Blinds</span></div>
    </div>
    <div class="frame">
      <div class="frame__bottom">
        <span class="frame__line frame__line--lead"></span>
        <span class="frame__caption">Custom Plantation Shutters &amp; Motorized Architectural Shading Systems</span>
        <span class="frame__line frame__line--rest"></span>
      </div>
    </div>
  </section>

  <section class="card card--back" aria-label="Card back">
    <div class="back-brand">
      <div class="brand-name">Gilded<br>Slatworks</div>
      <div class="brand-lines"><span>Shutters</span><span>Shades</span><span>Blinds</span></div>
    </div>
    <div class="divider"></div>
    <div class="contact">
      <div class="contact__name">Daniel Trevick</div>
      <div class="contact__role">Owner</div>
      <ul class="contact__list">
        <li class="contact__item">
          <svg class="contact__icon" viewBox="0 0 16 16" aria-hidden="true"><path fill="#c9a44a" d="M3.5 1h2.2l1.2 3.2-1.6 1.2a8.5 8.5 0 0 0 5.3 5.3l1.2-1.6L15 10.3v2.2c0 1.4-1.1 2.5-2.5 2.5C6.7 15 1 9.3 1 3.5 1 2.1 2.1 1 3.5 1z"/></svg>
          <span>919-555-0148</span>
        </li>
        <li class="contact__item">
          <svg class="contact__icon" viewBox="0 0 16 16" aria-hidden="true"><g fill="none" stroke="#c9a44a" stroke-width="1.4"><circle cx="8" cy="8" r="6.5"/><ellipse cx="8" cy="8" rx="2.8" ry="6.5"/><path d="M1.5 8h13"/></g></svg>
          <span>gildedslatworks.com</span>
        </li>
      </ul>
    </div>
    <div class="frame">
      <div class="frame__bottom">
        <span class="frame__line frame__line--lead"></span>
        <span class="frame__caption">Custom Interior &amp; Exterior Window Treatments</span>
        <span class="frame__line frame__line--rest"></span>
      </div>
    </div>
  </section>

</main>
</body>
</html>
```